Visitenkarten/Briefpaier/Kassenkassenbelege für Juwelier
Zielgruppe
Mittelständischer Juwelier mit zwei Filialen. Klassischer Schmuck, Uhren und Modeschmuck
Aufgabenstellung
Es müssen für zwei Geschäfte Visitenkarten, Briefpapier (A4) und Kassenkassenbelege (A6) erstellt werden. Logo und Typo im Anhang. Ein Farbkonzept besteht noch nicht. Die Idee geht in Richtung Bordeaux-Rot.
Generell:
(1) Sieht erstmal nach viel Beschreibung aus, bitte nicht entmutigen lassen, sind zu 90% nur austauschbare Inhalts-/Kontaktdaten.
(2) Für meine Zwecke reicht es vollkommen aus, wenn bei den Vorschlägen zur Arbeitsersparnis erstmal nur mit einer Adresse gearbeitet wird. Wenn ich dann den zutreffenden Designvorschlag gefunden habe, können wir die zweite Adresse in dem ersten Format umsetzen. Ich denke das spart Zeit und Nerven.
(3) Bitte Angaben wie "Tel.:" oder "USt.- ID:" nicht wörtlich nehmen, es soll dabei klar sein worum es geht; wenn "Telefon" ausgeschrieben besser aussieht, bitte in der optisch ansprechenderen Form verwenden.
(4) Bei Fragen, bitte fragen!
(5) Viel Spass bei dem Projekt - Ich freu' mich auf die Vorschläge!
Visitenkarten(1):
Juwelier Brenneck GmbH
www.juwelier-brenneck-beispiel.de
Visitenkarten(2):
Visitenkarten(generell):
(1) Die einzelnen Daten können durch Hervorhebungen wie Adresse, Kontakt, Online/Internet unterteilt bzw. hervorgehoben werden.
(2) Die Visitenkarten sollen farbig gedruckt werden; geplant ist weiß als Hintergrund ist aber nicht zwingend bei einer guten anderen Idee
Briefpapier:
(1)Absender im Adressfeld für DIN-lang Briefumschläge mit Fenster:
(2)Informationen im Footer/Seitenbereich:
Juwelier Brenneck Gmb..

```html
<!DOCTYPE html>
<html lang="de">
<head>
<meta charset="utf-8">
<title>Juwelier Brenneck – Geschäftsausstattung</title>
<link href="https://fonts.googleapis.com/css2?family=Source+Sans+3:wght@400;600&display=swap" rel="stylesheet">
<style>
  :root {
    --bg: #f7f7f7;
    --paper: #ffffff;
    --navy: #0d3b4f;
    --taupe: #7d7369;
    --rule: #8a8077;
    --mark: #555555;
    --divider: #cfcac5;
  }
  * { margin: 0; padding: 0; box-sizing: border-box; }
  html, body { width: 1200px; height: 1000px; overflow: hidden; background: var(--bg); }
  body { position: relative; font-family: "Source Sans 3", "Source Sans Pro", sans-serif; color: var(--taupe); }

  .crop-mark { position: absolute; background: var(--mark); }
  .crop-mark.v { width: 1px; height: 25px; }
  .crop-mark.h { height: 1px; width: 25px; }

  .letterhead {
    position: absolute; left: 42px; top: 50px; width: 533px; height: 753px;
    background: var(--paper); box-shadow: 2px 2px 4px rgba(0,0,0,.25);
  }
  .brand-name { position: absolute; font-weight: 600; color: var(--taupe); letter-spacing: 1px; white-space: nowrap; }
  .letterhead .brand-name { right: 23px; top: 104px; font-size: 19px; }

  .sender-block { position: absolute; right: 23px; top: 137px; text-align: right; font-size: 7.6px; line-height: 10.8px; }
  .sender-block .company { font-size: 9.6px; line-height: 12px; font-weight: 400; }
  .sender-block .contact { margin-top: 10px; }

  .fold-mark { position: absolute; left: 0; width: 18px; height: 1px; background: var(--divider); }

  .footer { position: absolute; left: 0; right: 0; top: 706px; border-top: 2px solid var(--rule); height: 47px; }
  .footer-col { position: absolute; font-size: 6.4px; line-height: 8px; top: 6px; }
  .footer-col.bank { left: 65px; }
  .footer-col.tax { left: 246px; top: 10px; }
  .footer-col.branch { left: 411px; top: 8px; font-size: 7.2px; line-height: 8.2px; }
  .footer-divider { position: absolute; top: 4px; width: 1px; height: 30px; background: var(--divider); }

  .envelope {
    position: absolute; left: 622px; width: 559px; background: var(--paper);
    box-shadow: 2px 2px 4px rgba(0,0,0,.25);
  }
  .envelope.front { top: 100px; height: 286px; border-bottom: 6px solid var(--rule); }
  .envelope.back { top: 475px; height: 285px; }

  .return-address { position: absolute; left: 34px; top: 26px; font-size: 7.4px; line-height: 10.8px; }
  .return-address .company { color: var(--navy); font-weight: 600; font-size: 9.2px; line-height: 11px; }

  .address-window {
    position: absolute; left: 39px; top: 153px; width: 223px; height: 89px;
    border-radius: 10px; background: var(--paper);
    box-shadow: inset 2px 2px 3px rgba(0,0,0,.3);
  }
  .envelope.front .brand-name { left: 448px; transform: translateX(-50%); top: 184px; font-size: 17px; }

  .flap { position: absolute; left: 0; top: 0; }
</style>
</head>
<body>
  <span class="crop-mark v" style="left:42px;top:12px"></span>
  <span class="crop-mark v" style="left:575px;top:12px"></span>
  <span class="crop-mark v" style="left:42px;top:816px"></span>
  <span class="crop-mark v" style="left:575px;top:816px"></span>
  <span class="crop-mark h" style="left:4px;top:50px"></span>
  <span class="crop-mark h" style="left:588px;top:50px"></span>
  <span class="crop-mark h" style="left:4px;top:803px"></span>
  <span class="crop-mark h" style="left:588px;top:803px"></span>

  <section class="letterhead">
    <span class="brand-name">Juwelier Brenneck</span>

    <div class="sender-block">
      <div class="company">Juwelier Brenneck GmbH</div>
      <div>Lindenallee 12</div>
      <div>45100 Musterstadt</div>
      <div class="contact">
        <div>Tel.: 0201-100200</div>
        <div>Fax: 0201-100201</div>
        <div>info@juwelier-brenneck-beispiel.de</div>
        <div>www.juwelier-brenneck-beispiel.de</div>
      </div>
    </div>

    <span class="fold-mark" style="top:268px"></span>
    <span class="fold-mark" style="top:520px"></span>

    <footer class="footer">
      <div class="footer-col bank">Bankverbindung:<br>Beispielbank AG Musterstadt<br>IBAN: DE00 1234 5678 0000 1111 22<br>BIC: BSPB DE 00</div>
      <span class="footer-divider" style="left:208px"></span>
      <div class="footer-col tax">Steuernummer:<br>123/4567/8900<br>USt.- ID: DE 000111222</div>
      <span class="footer-divider" style="left:349px"></span>
      <div class="footer-col branch">Filiale:<br>Am Markt 5<br>45200 Beispielheim</div>
    </footer>
  </section>

  <section class="envelope front">
    <div class="return-address">
      <div class="company">Juwelier Brenneck GmbH</div>
      <div>Lindenallee 12</div>
      <div>45100 Musterstadt</div>
    </div>
    <div class="address-window"></div>
    <span class="brand-name">Juwelier Brenneck</span>
  </section>

  <section class="envelope back">
    <svg class="flap" width="559" height="70" viewBox="0 0 559 70">
      <path d="M0 2 L28 52 Q34 62 46 62 L508 62 Q520 62 528 54 L559 4" fill="none" stroke="#e3e3e3" stroke-width="1.5"/>
    </svg>
  </section>
</body>
</html>
```